Valdane Companies Business Card Design

We need a new business card for our Private Equity Real Estate Development firm, “Valdane” and our EB-5 regional center “Thornmere Regional Center” on one card. We prefer a design that is simple, elegant, and represents the luxury products we design and build as well as the financial security and stability our successful history has produced. We are an industry leader in our field and 3rd generation family business that has evolved into an institutional quality investment platform. Considered design size is standard business card dimensions (3.5 x 2 inches with an additional 1/8 inch space for design elements or backgrounds that extend beyond the finished size of your piece.

Target Market(s)

• High net worth individuals
• Highly skilled technical workers and physicians in the US seeking investment-based immigration opportunities
• Sophisticated private equity investors
• Intermediary partners include domestic attorneys and investment brokers, as well as international agent networks
• US real estate developers

Industry/Entity Type

Finance

Contact Information for Business Card

(Providing placeholder info for personal information, please design for longer character spaces, longer names and addresses etc..)
• Logo for Valdane
• Logo for Thornmere Regional Center
• Full name: Marcus Valdane
• Job title: CEO
• Email address: mvaldane@valdanecompanies.com
• Cell phone number: +1.555.314.2287
• Office number +1.555.628.4410
• Office address: Larkfield Court 5, 4817 Vista Orilla, Alder Vale, CA.
• Website: www.valdanecompanies.com

Font styles to use
Serif
Sans Serif

Colors
ec1f27
ffffff
000000

Requirements
Must have
• • Logo for Valdane
• • Logo for Thornmere Regional Center
• - Use rounded corners
• (See .ai file included for logos)
Nice to have
• • Simple, elegant design
• • Aesthetically compatible with our website design (www.valdanecompanies.com)
• • Color palette including but not limited to white, black, and red (as per logos)
Should not have
• - Not too much red color
• - Do not stack both logos on top of each other

```html
<!DOCTYPE html>
<html lang="en">
<head>
<meta charset="utf-8">
<title>Valdane Companies Business Card</title>
<link rel="stylesheet" href="https://fonts.googleapis.com/css2?family=Cinzel:wght@400;700&family=EB+Garamond:wght@400;500&display=swap">
<style>
  :root {
    --stage: #2f2f31;
    --card-white: #ffffff;
    --card-black: #0d0d0d;
    --card-black-edge: #1c1c1c;
    --ink: #1a1a1a;
    --ink-soft: #3b3b3b;
    --emboss: #3a3a3c;
    --brand-red: #a51c30;
    --rule-grey: #9a9a9a;
    --ring-grey: #cfcfcf;
  }
  * { box-sizing: border-box; margin: 0; padding: 0; }
  html, body { width: 1200px; height: 1000px; overflow: hidden; }
  body {
    background: var(--stage);
    font-family: "EB Garamond", Georgia, serif;
    position: relative;
  }
  .card {
    position: absolute;
    left: 250px;
    width: 700px;
    height: 400px;
    border-radius: 28px;
    overflow: hidden;
  }

  /* Back side */
  .card-back {
    top: 60px;
    background: radial-gradient(ellipse at 50% 40%, var(--card-black-edge), var(--card-black) 75%);
  }
  .back-name {
    position: absolute;
    left: 0; right: 0; top: 135px;
    text-align: center;
    font-family: "Cinzel", serif;
    font-weight: 700;
    color: var(--emboss);
  }
  .back-name .primary { display: block; font-size: 78px; letter-spacing: 2px; line-height: 1; }
  .back-name .secondary { display: block; font-size: 26px; letter-spacing: 18px; margin-top: 14px; padding-left: 18px; }

  /* Front side */
  .card-front {
    top: 540px;
    background: var(--card-white);
  }
  .brand-main {
    position: absolute;
    left: 38px; top: 34px;
    display: flex; align-items: center; gap: 14px;
  }
  .brand-main .mark { width: 40px; height: 40px; background: var(--ink-soft); }
  .brand-main .name {
    font-family: "Cinzel", serif; font-weight: 700;
    font-size: 44px; color: var(--ink); letter-spacing: 1px;
  }
  .brand-partner {
    position: absolute;
    right: 34px; top: 118px;
    display: flex; align-items: center; gap: 10px;
  }
  .brand-partner .mark { width: 34px; height: 34px; background: var(--brand-red); }
  .brand-partner .name {
    font-family: "Cinzel", serif; font-weight: 700;
    font-size: 17px; line-height: 1.15; color: var(--brand-red);
  }
  .person {
    position: absolute;
    left: 0; right: 0; top: 186px;
    text-align: center;
    font-family: "Cinzel", serif;
  }
  .person .full-name { font-weight: 700; font-size: 26px; color: var(--brand-red); letter-spacing: 0.5px; }
  .person .role { font-size: 14px; color: var(--ink); margin-top: 2px; }

  .contacts {
    position: absolute;
    left: 34px; right: 34px; top: 252px;
    display: flex; justify-content: space-between;
  }
  .contact { text-align: center; }
  .contact .icon {
    width: 38px; height: 38px; margin: 0 auto 6px;
    border-radius: 50%;
    background: var(--brand-red);
    box-shadow: 0 0 0 3px var(--ring-grey);
    display: flex; align-items: center; justify-content: center;
  }
  .contact .value { font-size: 14px; color: var(--ink); white-space: nowrap; }
  .contact .value .accent { color: var(--brand-red); }

  .rule {
    position: absolute; left: 0; right: 0; top: 326px;
    height: 5px;
    border-top: 2px solid var(--rule-grey);
    border-bottom: 1px solid var(--rule-grey);
  }
  .footer-band {
    position: absolute; left: 0; right: 0; bottom: 0; height: 66px;
    background: var(--brand-red);
    display: flex; align-items: center; justify-content: center;
  }
  .footer-band .address { color: var(--card-white); font-size: 18px; letter-spacing: 0.5px; }
</style>
</head>
<body>

  <section class="card card-back" aria-label="Card back">
    <div class="back-name">
      <span class="primary">VALDANE</span>
      <span class="secondary">CAPITAL</span>
    </div>
  </section>

  <section class="card card-front" aria-label="Card front">
    <div class="brand-main">
      <span class="mark"></span>
      <span class="name">VALDANE</span>
    </div>

    <div class="brand-partner">
      <span class="mark"></span>
      <span class="name">THORNMERE<br>REGIONAL CENTER</span>
    </div>

    <div class="person">
      <div class="full-name">MARCUS VALDANE</div>
      <div class="role">CEO</div>
    </div>

    <div class="contacts">
      <div class="contact">
        <div class="icon">
          <svg width="20" height="20" viewBox="0 0 24 24"><path fill="#fff" d="M6.6 10.8a15 15 0 0 0 6.6 6.6l2.2-2.2a1 1 0 0 1 1-.25 11.4 11.4 0 0 0 3.6.57 1 1 0 0 1 1 1V20a1 1 0 0 1-1 1A17 17 0 0 1 3 4a1 1 0 0 1 1-1h3.5a1 1 0 0 1 1 1c0 1.25.2 2.45.57 3.6a1 1 0 0 1-.25 1z"/></svg>
        </div>
        <div class="value">+1.555.314.2287</div>
      </div>
      <div class="contact">
        <div class="icon">
          <svg width="20" height="20" viewBox="0 0 24 24"><rect x="6.5" y="2" width="11" height="20" rx="2" fill="none" stroke="#fff" stroke-width="2"/><circle cx="12" cy="18.5" r="1.2" fill="#fff"/></svg>
        </div>
        <div class="value">+1.555.628.4410</div>
      </div>
      <div class="contact">
        <div class="icon">
          <svg width="20" height="20" viewBox="0 0 24 24"><rect x="3" y="6" width="18" height="13" fill="none" stroke="#fff" stroke-width="2"/><path d="M3 6l9 7 9-7" fill="none" stroke="#fff" stroke-width="2"/></svg>
        </div>
        <div class="value">mvaldane@valdanecompanies.com</div>
      </div>
      <div class="contact">
        <div class="icon">
          <svg width="20" height="20" viewBox="0 0 24 24" fill="none" stroke="#fff" stroke-width="1.6"><circle cx="12" cy="12" r="9"/><ellipse cx="12" cy="12" rx="4" ry="9"/><path d="M3 12h18M5 7h14M5 17h14"/></svg>
        </div>
        <div class="value">www.<span class="accent">valdanecompanies</span>.com</div>
      </div>
    </div>

    <div class="rule"></div>
    <div class="footer-band">
      <span class="address">Larkfield Court 5, 4817 Vista Orilla, Alder Vale, CA.</span>
    </div>
  </section>

</body>
</html>
```